Brightwave Reach - Business Card

We need a business card for a Social Media Marketing company that specializes in online marketing for small businesses in Canada using common Social Media platforms such as Pixlora, Chatterly, Blinkpost & Quibber.

I have uploaded a copy of our logo which I would like utilized in the business card. We would like the business card to be modern yet classy design.

Our website is www.brightwavereach.ca

Industry/Entity Type

Marketing

Contact Information for Business Card

Email: info@brightwavereach.ca
Website: www.brightwavereach.ca
Telephone: 604-555-0193

Colors

Designer to choose colors to be used in the design.

Requirements
Must have
• Social Media icons on reverse
• Please add some designs with color.

```html
<!DOCTYPE html>
<html lang="en">
<head>
<meta charset="utf-8">
<title>Brightwave Reach – Business Card</title>
<link href="https://fonts.googleapis.com/css2?family=Open+Sans:wght@400;600;700&display=swap" rel="stylesheet">
<style>
  :root {
    --page-bg: #e8e6e3;
    --card-bg: #3b4043;
    --card-ink: #ffffff;
    --card-ink-soft: #eceeee;
    --rule: #cfd3d4;
    --accent: #c8372d;
  }
  * { margin: 0; padding: 0; box-sizing: border-box; }
  html, body {
    width: 1200px; height: 900px; overflow: hidden;
    background: var(--page-bg);
    font-family: "Open Sans", Arial, sans-serif;
  }
  .canvas { position: relative; width: 1200px; height: 900px; }

  .card {
    position: absolute;
    background: var(--card-bg);
    color: var(--card-ink);
    text-align: center;
  }

  .brand-name {
    font-weight: 700;
    text-transform: uppercase;
    line-height: 1;
    letter-spacing: 0.5px;
  }
  .brand-name span { display: block; margin-bottom: 4px; }

  /* front side */
  .card--front { left: 78px; top: 35px; width: 588px; height: 363px; }
  .card--front .brand-name {
    position: absolute; left: 0; right: 0; top: 60px;
    font-size: 46px;
  }
  .holder { position: absolute; left: 0; right: 0; top: 212px; }
  .holder-name { font-size: 19px; font-weight: 700; text-transform: uppercase; }
  .holder-role { font-size: 15px; color: var(--card-ink-soft); margin-top: 1px; }
  .holder-rule {
    position: absolute; left: 200px; top: 279px;
    width: 188px; height: 1px; background: var(--rule);
  }
  .contact {
    position: absolute; left: 0; right: 0; top: 308px;
    font-size: 15px; color: var(--card-ink-soft);
  }
  .contact b { font-weight: 700; }
  .contact .item + .item { margin-left: 18px; }

  /* back side */
  .card--back { left: 388px; top: 505px; width: 566px; height: 352px; }
  .card--back .brand-name {
    position: absolute; left: 0; right: 0; top: 108px;
    font-size: 40px;
  }
  .website {
    position: absolute; left: 0; right: 0; top: 276px;
    font-size: 16px; letter-spacing: 0.3px;
  }
  .social-list {
    position: absolute; left: 0; right: 0; top: 314px;
    display: flex; justify-content: center; gap: 22px;
    list-style: none;
    font-size: 12px; color: var(--card-ink-soft);
  }
  .social-item { display: flex; align-items: center; gap: 6px; }
  .social-dot {
    width: 9px; height: 9px; border-radius: 50%;
    background: var(--accent);
  }
</style>
</head>
<body>
<main class="canvas">

  <section class="card card--front" aria-label="Business card front">
    <h1 class="brand-name"><span>Brightwave</span><span>Reach</span></h1>
    <div class="holder">
      <p class="holder-name">Marcus Ellery</p>
      <p class="holder-role">Managing Director</p>
    </div>
    <div class="holder-rule"></div>
    <p class="contact">
      <span class="item"><b>P:</b> 604-555-0193</span>
      <span class="item"><b>E:</b> info@brightwavereach.ca</span>
    </p>
  </section>

  <section class="card card--back" aria-label="Business card back">
    <h2 class="brand-name"><span>Brightwave</span><span>Reach</span></h2>
    <p class="website">www.brightwavereach.ca</p>
    <ul class="social-list">
      <li class="social-item"><span class="social-dot"></span>Pixlora</li>
      <li class="social-item"><span class="social-dot"></span>Chatterly</li>
      <li class="social-item"><span class="social-dot"></span>Blinkpost</li>
      <li class="social-item"><span class="social-dot"></span>Quibber</li>
    </ul>
  </section>

</main>
</body>
</html>
```